Business Card Design (NEW FILES)

ATTENTION: New vector files are available. Please update your design to reflect/use the new (better resolution) logo images.

Seeking a unique and professional business card design for a commercial drone photography/videography business. The layout should feature
the logo (attached) and include the following information:
Owen Tarrick
614-502-7738
www.skylarkreelworks.example
NRD Certified Remote Pilot

Owen Tarrick

```html
<!DOCTYPE html>
<html lang="en">
<head>
<meta charset="utf-8">
<title>Skylark Reelworks – Business Card</title>
<link href="https://fonts.googleapis.com/css2?family=Poppins:wght@400;600&display=swap" rel="stylesheet">
<style>
  :root {
    --navy: #131a45;
    --navy-soft: #2b336a;
    --orange: #ef8c50;
    --white: #ffffff;
    --backdrop: #adadad;
  }
  * { box-sizing: border-box; margin: 0; padding: 0; }
  html, body {
    width: 1093px;
    height: 1200px;
    overflow: hidden;
    background: var(--backdrop);
    font-family: "Poppins", sans-serif;
  }
  .card {
    position: absolute;
    left: 264px;
    width: 580px;
    height: 356px;
    border-radius: 22px;
    overflow: hidden;
  }
  .card--front { top: 226px; background: var(--white); }
  .card--back  { top: 621px; background: var(--navy); }

  .front-band {
    position: absolute;
    left: 0; right: 0; bottom: 0;
    height: 64px;
    background: var(--navy);
  }
  .drone-art {
    position: absolute;
    left: 57px;
    top: 36px;
    width: 523px;
    height: 320px;
    border-radius: 160px 0 0 0;
    background: linear-gradient(160deg, rgba(19,26,69,0.08) 0%, rgba(19,26,69,0.35) 55%, var(--navy-soft) 100%);
  }
  .holder-name {
    position: absolute;
    left: 38px;
    top: 196px;
    font-size: 25px;
    font-weight: 600;
    color: var(--navy);
    letter-spacing: 0.2px;
  }
  .holder-title {
    position: absolute;
    left: 38px;
    top: 228px;
    font-size: 13.5px;
    font-weight: 400;
    color: var(--orange);
  }
  .holder-phone {
    position: absolute;
    left: 39px;
    top: 251px;
    font-size: 16px;
    color: var(--navy);
  }
  .holder-web {
    position: absolute;
    left: 40px;
    top: 303px;
    font-size: 17px;
    color: var(--white);
    letter-spacing: 0.6px;
  }

  .brand-name {
    position: absolute;
    left: 0; right: 0;
    top: 110px;
    text-align: center;
    font-size: 42px;
    font-weight: 400;
    line-height: 1.1;
    color: var(--white);
    letter-spacing: 2px;
  }
  .services {
    position: absolute;
    left: 0; right: 0;
    top: 290px;
    text-align: center;
    font-size: 17px;
    line-height: 21px;
    color: var(--white);
  }
  .services-note { color: var(--orange); }
</style>
</head>
<body>
  <section class="card card--front">
    <div class="drone-art" role="img" aria-label="Illustration of a navy drone with spinning rotors and a camera gimbal"></div>
    <div class="front-band"></div>
    <h1 class="holder-name">OWEN TARRICK</h1>
    <p class="holder-title">NRD CERTIFIED REMOTE PILOT</p>
    <p class="holder-phone">614-502-7738</p>
    <p class="holder-web">www.skylarkreelworks.example</p>
  </section>

  <section class="card card--back">
    <h2 class="brand-name">SKYLARK<br>REELWORKS</h2>
    <div class="services">
      <p>Drone Photography and Videography Services</p>
      <p class="services-note">High Quality | Fully Insured</p>
    </div>
  </section>
</body>
</html>
```